Plumbing Product Supply Company Needs Front & Back Cover Design For Instruction Manuals

We need a front and back over design for our instruction manuals that we need to give to clients.

There will also be a picture of the product on the front cover so please use the supplied image as dummy.

it needs to incorporate our logo and branding colours.

We are the industry leader so it needs to be up-market, professional and stand out from the crowd.

Target Market(s)

Plumbing Companies

Industry/Entity Type

Plumbing

Font styles to use
Sans Serif

Colors
abd036
ffffff
000000
eaeaea
cbcbcb

Requirements
Must have
• Front & Back Cover as it will become a booklet.
• The logo is to be on the black background.
Nice to have
• Professional, modern, sleek.
Should not have
• Other colours that what is on the guidelines.

```html
<!DOCTYPE html>
<html lang="en">
<head>
<meta charset="utf-8">
<title>Southern Relining Supplies – Manual Covers</title>
<link href="https://fonts.googleapis.com/css2?family=Josefin+Sans:wght@400&family=Lato:wght@400;700&display=swap" rel="stylesheet">
<style>
  :root {
    --brand-green: #abd036;
    --brand-green-deep: #7fa82a;
    --white: #ffffff;
    --black: #000000;
    --light-grey: #eaeaea;
    --mid-grey: #cbcbcb;
    --backdrop: #2a2a2a;
  }
  * { box-sizing: border-box; margin: 0; padding: 0; }
  html, body { width: 1200px; height: 789px; overflow: hidden; }
  body {
    background: var(--backdrop);
    font-family: "Lato", sans-serif;
    display: flex;
    align-items: center;
    justify-content: center;
  }
  .booklet-spread {
    display: flex;
    width: 990px;
    height: 700px;
  }
  .cover {
    position: relative;
    width: 495px;
    height: 700px;
    overflow: hidden;
  }
  .back-cover {
    background: var(--black);
    color: var(--white);
  }
  .brand-name {
    font-family: "Josefin Sans", sans-serif;
    font-weight: 400;
    color: var(--brand-green);
    text-align: center;
    letter-spacing: 0.06em;
    text-transform: uppercase;
    line-height: 1.15;
  }
  .back-cover .brand-name {
    position: absolute;
    top: 240px;
    left: 0;
    width: 100%;
    font-size: 34px;
  }
  .contact-block {
    position: absolute;
    bottom: 70px;
    left: 0;
    width: 100%;
    text-align: center;
  }
  .contact-title {
    font-size: 17px;
    font-weight: 700;
    margin-bottom: 6px;
  }
  .contact-line {
    font-size: 9.5px;
    line-height: 1.5;
  }
  .front-cover {
    background: var(--light-grey);
  }
  .front-artwork {
    position: absolute;
    inset: 0;
  }
  .front-cover .brand-name {
    position: absolute;
    top: 78px;
    left: 0;
    width: 100%;
    font-size: 30px;
  }
  .product-photo {
    position: absolute;
    top: 295px;
    left: 60px;
    width: 380px;
    height: 290px;
    border-radius: 6px;
    background: radial-gradient(ellipse at 50% 50%, #6c6c6c 0%, #8e9a7a 35%, #d8d8d8 75%, var(--light-grey) 100%);
  }
</style>
</head>
<body>
  <main class="booklet-spread">
    <section class="cover back-cover" aria-label="Back cover">
      <h2 class="brand-name">Southern Relining<br>Supplies</h2>
      <address class="contact-block">
        <p class="contact-title">Contact Us:</p>
        <p class="contact-line">Lorem ipsum Lorem ipsum Lorem ipsum Lorem ipsum Lorem ipsum</p>
        <p class="contact-line">Email: hello@southernrelining.example | Ph: 000 000 0000 | Fax: 000 000 0000</p>
      </address>
    </section>

    <section class="cover front-cover" aria-label="Front cover">
      <svg class="front-artwork" width="495" height="700" viewBox="0 0 495 700" aria-hidden="true">
        <path d="M0 0 H495 V190 C420 230 330 205 220 225 C130 240 60 250 0 300 Z" fill="var(--black)"/>
        <path d="M0 318 C70 262 150 250 240 240 C340 228 420 232 495 200" fill="none" stroke="var(--brand-green)" stroke-width="6"/>
        <path d="M0 334 C80 282 170 266 260 258 C360 250 430 246 495 218" fill="none" stroke="var(--brand-green-deep)" stroke-width="3"/>
        <path d="M0 660 C160 650 330 630 495 590 V700 H0 Z" fill="var(--mid-grey)"/>
        <path d="M0 662 C160 652 330 632 495 592" fill="none" stroke="var(--white)" stroke-width="3"/>
      </svg>
      <h1 class="brand-name">Southern Relining<br>Supplies</h1>
      <div class="product-photo" role="img" aria-label="Product photo: pipe relining kit with tool case, resin containers, liner rolls, blue hose and green push rods"></div>
    </section>
  </main>
</body>
</html>
```